Veldmark Supplies Business Card

Professional business card that stand out to our potential customers. Front and back with clean modern design

Industry/Entity Type

Oil and gas

Contact Information for Business Card

Name, address, website , office phone and cell number

Requirements
Must have
• Editable files for each employee

```html
<!DOCTYPE html>
<html lang="en">
<head>
<meta charset="utf-8">
<title>Veldmark Supplies – Business Card</title>
<link rel="stylesheet" href="https://fonts.googleapis.com/css2?family=Lato:wght@400;700&display=swap">
<style>
  :root {
    --brand-red: #f50b0b;
    --brand-blue: #06afd3;
    --ink: #1b1b1b;
    --card: #ffffff;
    --backdrop: #e9eaec;
  }
  * { box-sizing: border-box; margin: 0; padding: 0; }
  html, body { width: 1200px; height: 694px; overflow: hidden; }
  body {
    background: var(--backdrop);
    font-family: "Lato", Arial, sans-serif;
    color: var(--ink);
    position: relative;
  }
  .card {
    position: absolute;
    top: 192px;
    width: 540px;
    height: 310px;
    background: var(--card);
    border-radius: 22px;
    overflow: hidden;
    box-shadow: 0 6px 22px rgba(0,0,0,.14);
  }
  .card--front { left: 36px; }
  .card--back { left: 624px; }

  /* brand wordmark */
  .wordmark {
    display: flex;
    align-items: center;
    gap: 12px;
    color: var(--brand-red);
    font-weight: 700;
    text-transform: uppercase;
    letter-spacing: .06em;
    white-space: nowrap;
  }
  .wordmark__square { background: var(--brand-red); flex: none; }

  .card--front .wordmark {
    position: absolute;
    left: 50%; top: 50%;
    transform: translate(-50%, -50%);
    font-size: 34px;
  }
  .card--front .wordmark__square { width: 34px; height: 34px; }

  .card--back .wordmark {
    position: absolute;
    right: 34px; top: 40px;
    font-size: 19px;
    gap: 9px;
  }
  .card--back .wordmark__square { width: 20px; height: 20px; }

  /* back details */
  .person { position: absolute; left: 36px; top: 132px; }
  .person__name { color: var(--brand-red); font-weight: 700; font-size: 30px; line-height: 1.1; }
  .person__role { font-size: 17px; margin-top: 4px; }

  .divider {
    position: absolute; left: 36px; right: 34px; top: 196px;
    height: 1.5px; background: var(--ink);
  }

  .contact-list { list-style: none; font-size: 15px; line-height: 1; }
  .contact-list li { display: flex; align-items: center; gap: 9px; height: 21px; }
  .contact-list svg { width: 14px; height: 14px; flex: none; fill: var(--brand-blue); }
  .contact-list--left { position: absolute; left: 36px; top: 208px; }
  .contact-list--right { position: absolute; right: 34px; top: 208px; text-align: right; }
  .contact-list--right li { justify-content: flex-end; }
  .contact-list--right .address li { padding-right: 23px; }

  .base-band {
    position: absolute; left: 0; right: 0; bottom: 0; height: 7px;
    display: flex;
  }
  .base-band__red { flex: 4; background: var(--brand-red); }
  .base-band__blue { flex: 1; background: var(--brand-blue); }
</style>
</head>
<body>

  <section class="card card--front" aria-label="Card front">
    <div class="wordmark"><span class="wordmark__square"></span>Veldmark Supplies</div>
  </section>

  <section class="card card--back" aria-label="Card back">
    <div class="wordmark"><span class="wordmark__square"></span>Veldmark Supplies</div>

    <div class="person">
      <p class="person__name">Daniel Harrow</p>
      <p class="person__role">Owner</p>
    </div>

    <div class="divider"></div>

    <ul class="contact-list contact-list--left">
      <li>
        <svg viewBox="0 0 24 24"><path d="M6.6 10.8a15.1 15.1 0 0 0 6.6 6.6l2.2-2.2c.3-.3.7-.4 1-.2 1.1.4 2.3.6 3.6.6.6 0 1 .4 1 1V20c0 .6-.4 1-1 1A17 17 0 0 1 3 4c0-.6.4-1 1-1h3.5c.6 0 1 .4 1 1 0 1.3.2 2.5.6 3.6.1.3 0 .7-.2 1z"/></svg>
        055-610 204 318
      </li>
      <li>
        <svg viewBox="0 0 24 24"><path d="M7 1h10a2 2 0 0 1 2 2v18a2 2 0 0 1-2 2H7a2 2 0 0 1-2-2V3a2 2 0 0 1 2-2zm0 3v15h10V4zm5 16.2a1 1 0 1 0 0 2 1 1 0 0 0 0-2z"/></svg>
        055-610 947 226
      </li>
      <li>
        <svg viewBox="0 0 24 24"><path d="M2 5h20v14H2zm2 2v.5l8 5.5 8-5.5V7z"/></svg>
        office@veldmark.com
      </li>
    </ul>

    <ul class="contact-list contact-list--right">
      <li>
        www.veldmark.com
        <svg viewBox="0 0 24 24"><path d="M12 2a10 10 0 1 0 0 20 10 10 0 0 0 0-20zm-1 17.9A8 8 0 0 1 4.1 11H8c0 3 1.2 6.2 3 8.9zM8 9H4.1A8 8 0 0 1 11 4.1C9.2 6.8 8 9 8 9zm5 10.9c1.8-2.7 3-5.9 3-8.9h3.9a8 8 0 0 1-6.9 8.9zM16 9c0 0-1.2-2.2-3-4.9A8 8 0 0 1 19.9 9z"/></svg>
      </li>
      <li>
        87, Quarry Road Unit 4
        <svg viewBox="0 0 24 24"><path d="M12 2a7 7 0 0 0-7 7c0 5.2 7 13 7 13s7-7.8 7-13a7 7 0 0 0-7-7zm0 9.5a2.5 2.5 0 1 1 0-5 2.5 2.5 0 0 1 0 5z"/></svg>
      </li>
      <li style="padding-right:23px">79705, Texas USA</li>
    </ul>

    <div class="base-band"><span class="base-band__red"></span><span class="base-band__blue"></span></div>
  </section>

</body>
</html>
```